Oriel Photography Business Card

I need a business card designed for a photography business based in Perth, Western Australia called Oriel Photography.

We specialise in wedding, event photography and portrait photography.

The business card must borrow the style of the attached logo.

The hex codes for the colours in the logo are:
#ED1D85 - Pink
#89C23E - Green
#37282F - Black

The name on the card will be:
Name: Tobrian
Phone: 0417395268
Website: www.orielphotography.example.com.au
Facebook: orielphotography

I am open and happy to accept creative concepts.

I’d like some space at the back for writing notes and appointment details.

```html
<!DOCTYPE html>
<html lang="en">
<head>
<meta charset="utf-8">
<title>Oriel Photography – Business Card</title>
<link href="https://fonts.googleapis.com/css2?family=Montserrat:wght@400;500;700&display=swap" rel="stylesheet">
<style>
  :root {
    --pink: #ED1D85;
    --green: #89C23E;
    --green-back: #A4C743;
    --ink: #1E1A1C;
    --grey: #6B6B6B;
    --rule: #B5B5B5;
    --paper: #FFFFFF;
    --stage: #ECEBE8;
  }
  * { margin: 0; padding: 0; box-sizing: border-box; }
  html, body { width: 1200px; height: 720px; overflow: hidden; }
  body {
    background: var(--stage);
    font-family: "Montserrat", sans-serif;
    position: relative;
  }
  .card {
    position: absolute;
    width: 520px;
    height: 300px;
    top: 210px;
    overflow: hidden;
    box-shadow: 0 4px 14px rgba(0,0,0,.12);
  }
  .card > svg { position: absolute; inset: 0; }

  /* Front */
  .card-front { left: 50px; background: var(--paper); }
  .brand {
    position: absolute;
    display: flex;
    flex-direction: column;
    align-items: center;
    gap: 14px;
  }
  .brand-front { left: 22px; top: 92px; }
  .brand-mark { width: 46px; height: 46px; border-radius: 50%; background: var(--pink); }
  .brand-name {
    font-size: 12px;
    font-weight: 400;
    letter-spacing: 6px;
    text-transform: uppercase;
    color: var(--grey);
    white-space: nowrap;
  }
  .divider {
    position: absolute;
    left: 290px; top: 30px;
    width: 1px; height: 92px;
    background: #CFCFCF;
  }
  .contact { position: absolute; left: 308px; top: 38px; }
  .contact-name {
    font-size: 17px;
    font-weight: 700;
    color: var(--pink);
    text-transform: uppercase;
    letter-spacing: .5px;
    margin-bottom: 8px;
  }
  .contact-line {
    display: flex; align-items: center; gap: 7px;
    font-size: 12.5px; color: #3A3A3A;
    margin-bottom: 5px;
  }
  .icon-square { width: 11px; height: 11px; background: var(--ink); }
  .front-web {
    position: absolute;
    right: 16px; top: 214px;
    font-size: 13.5px;
    color: var(--paper);
    letter-spacing: .2px;
    white-space: nowrap;
  }

  /* Back */
  .card-back { left: 630px; background: var(--green-back); }
  .brand-back { left: 0; right: 0; top: 24px; gap: 12px; }
  .brand-back .brand-mark { background: var(--ink); width: 40px; height: 40px; }
  .brand-back .brand-name { color: var(--ink); }
  .notes-box {
    position: absolute;
    left: 30px; top: 108px;
    width: 462px; height: 146px;
    background: var(--paper);
    padding: 14px 16px 0 16px;
  }
  .notes-line { height: 21px; border-bottom: 1px dotted var(--rule); }
  .notes-label {
    position: absolute;
    left: 14px; top: 88px;
    font-size: 16px;
    color: var(--ink);
    background: var(--paper);
    padding-right: 6px;
  }
  .back-web {
    position: absolute;
    left: 0; right: 0; top: 266px;
    text-align: center;
    font-size: 14px;
    letter-spacing: 2px;
    color: var(--ink);
  }
</style>
</head>
<body>

<section class="card card-front" aria-label="Business card front">
  <svg viewBox="0 0 520 300" width="520" height="300" aria-hidden="true">
    <path d="M0,238 L160,238 C186,238 186,204 212,204 L520,204 L520,262 L0,262 Z" fill="#1E1A1C"/>
    <rect x="0" y="262" width="520" height="14" fill="#89C23E"/>
  </svg>

  <div class="brand brand-front">
    <span class="brand-mark"></span>
    <span class="brand-name">Oriel Photography</span>
  </div>

  <div class="divider"></div>

  <div class="contact">
    <p class="contact-name">Tobrian</p>
    <p class="contact-line">
      <svg width="12" height="12" viewBox="0 0 24 24" aria-hidden="true">
        <circle cx="12" cy="12" r="11" fill="none" stroke="#89C23E" stroke-width="2"/>
        <path d="M8.5 6.5l2 2.2-1.2 1.6c.8 1.7 2 2.9 3.6 3.7l1.6-1.2 2.2 2-1.3 1.9C11 16.3 7.6 12.9 7 8.1z" fill="#89C23E"/>
      </svg>
      0417395268
    </p>
    <p class="contact-line"><span class="icon-square"></span>orielphotography</p>
  </div>

  <p class="front-web">www.orielphotography.example.com.au</p>
</section>

<section class="card card-back" aria-label="Business card back">
  <div class="brand brand-back">
    <span class="brand-mark"></span>
    <span class="brand-name">Oriel Photography</span>
  </div>

  <div class="notes-box">
    <div class="notes-line"></div>
    <div class="notes-line"></div>
    <div class="notes-line"></div>
    <div class="notes-line"></div>
    <div class="notes-line"></div>
    <div class="notes-line"></div>
    <span class="notes-label">notes:</span>
  </div>

  <p class="back-web">www.orielphotography.example.com.au</p>
</section>

</body>
</html>
```